Chimney Service company needs new business card design

We need a updated business card with our new logo added. We provide a full range of chimney services throughout Vermont and New Hampshire. The business card will be one sided and color. Attached is our current business card another document showing all the information we would like on the card.
We dont like a lot of flashy colors.... here is a link to our website to get an idea of our branding www.flueguardianvt.example

Target Market(s)

homeowners

Industry/Entity Type

Business

Contact Information for Business Card

See attached sheet for content.

Font styles to use
Serif
Sans Serif

Requirements
Must have
• all information provided on separate sheet
Should not have
• Additional information that may clogg up design

```html
<!DOCTYPE html>
<html lang="en">
<head>
<meta charset="utf-8">
<title>Flue Guardian – Business Card</title>
<link rel="stylesheet" href="https://fonts.googleapis.com/css2?family=Cinzel:wght@400;600&display=swap">
<style>
  :root {
    --page-bg: #3a3a3a;
    --card-white: #ffffff;
    --brand-red: #a50808;
    --band-dark: #2f2f2f;
    --ink-dark: #222222;
    --ink-light: #ffffff;
  }
  * { margin: 0; padding: 0; box-sizing: border-box; }
  html, body {
    width: 1200px; height: 1000px; overflow: hidden;
    background: var(--page-bg);
    font-family: "Cinzel", "Times New Roman", serif;
  }
  .business-card {
    position: absolute; left: 100px; top: 215px;
    width: 1000px; height: 571px;
    background: var(--card-white);
    overflow: hidden;
    box-shadow: 0 12px 30px rgba(0,0,0,.45);
  }
  .brand-block {
    position: absolute; left: 0; top: 0; width: 530px; height: 285px;
    display: flex; flex-direction: column; align-items: center; justify-content: center;
  }
  .brand-name {
    display: flex; align-items: center; gap: 14px;
    font-size: 42px; font-weight: 600; color: var(--ink-dark); letter-spacing: 1px;
    white-space: nowrap;
  }
  .brand-square { width: 28px; height: 28px; background: var(--brand-red); }
  .brand-rule { width: 380px; height: 2px; background: var(--ink-dark); margin: 12px 0 14px; }
  .brand-tagline { font-size: 16px; color: var(--ink-dark); white-space: nowrap; }
  .services-block {
    position: absolute; left: 530px; top: 40px; height: 215px;
    border-left: 3px solid var(--brand-red);
    padding-left: 26px;
  }
  .services-title { font-size: 26px; font-weight: 600; color: var(--brand-red); margin-bottom: 10px; letter-spacing: 1px; }
  .services-list { list-style: none; }
  .services-list li {
    font-size: 21px; color: var(--ink-dark); line-height: 32px;
    display: flex; align-items: center; gap: 10px; white-space: nowrap;
  }
  .services-list li::before {
    content: ""; width: 9px; height: 9px; background: var(--brand-red); flex: none;
  }
  .trust-band {
    position: absolute; left: 0; top: 285px; width: 100%; height: 90px;
    background: var(--band-dark);
    display: flex; align-items: center; justify-content: center; gap: 22px;
    color: var(--ink-light); font-size: 26px; letter-spacing: 1px;
    border-bottom: 4px solid var(--card-white);
    white-space: nowrap;
  }
  .band-dot { width: 14px; height: 14px; border-radius: 50%; background: var(--ink-light); flex: none; }
  .contact-band {
    position: absolute; left: 0; top: 375px; width: 100%; height: 196px;
    background: var(--brand-red);
    display: flex; justify-content: space-around; align-items: center;
    color: var(--ink-light);
  }
  .contact-item { display: flex; flex-direction: column; align-items: center; gap: 14px; font-size: 21px; white-space: nowrap; }
  .contact-item svg { width: 44px; height: 44px; }
</style>
</head>
<body>
  <div class="business-card">
    <div class="brand-block">
      <div class="brand-name"><span class="brand-square"></span>Flue Guardian</div>
      <div class="brand-rule"></div>
      <div class="brand-tagline">Serving the Green Valley region since 1994</div>
    </div>

    <div class="services-block">
      <h2 class="services-title">Services We Provide</h2>
      <ul class="services-list">
        <li>Full Masonry Services</li>
        <li>Historic chimney restoration</li>
        <li>Stainless steel liners</li>
        <li>New Chimney installations</li>
        <li>NFSA Certified Chimney sweeps</li>
      </ul>
    </div>

    <div class="trust-band">
      <span>Fully Insured – Free Estimates</span>
      <span class="band-dot"></span>
      <span>Family Owned and Operated</span>
    </div>

    <div class="contact-band">
      <div class="contact-item">
        <svg viewBox="0 0 24 24" fill="none" stroke="#fff" stroke-width="1.8" stroke-linecap="round">
          <path d="M6 3l3 4-2 2c1 2.5 3.5 5 6 6l2-2 4 3-2 3c-7 0-14-7-14-14z" fill="#fff"/>
          <path d="M15 4a5 5 0 0 1 5 5M15 7a2 2 0 0 1 2 2"/>
        </svg>
        <span>802-555-0147</span>
      </div>
      <div class="contact-item">
        <svg viewBox="0 0 24 24" fill="none" stroke="#fff" stroke-width="1.8" stroke-linejoin="round">
          <rect x="3" y="8" width="18" height="13"/>
          <path d="M3 8l9 7 9-7"/>
          <path d="M7 10V3h10v7M9 6h6M9 8.5h6"/>
        </svg>
        <span>info@flueguardianvt.example</span>
      </div>
      <div class="contact-item">
        <svg viewBox="0 0 24 24" fill="none" stroke="#fff" stroke-width="1.6">
          <circle cx="12" cy="12" r="9"/>
          <ellipse cx="12" cy="12" rx="4" ry="9"/>
          <path d="M3 12h18M5 7h14M5 17h14"/>
        </svg>
        <span>www.flueguardianvt.example</span>
      </div>
    </div>
  </div>
</body>
</html>
```